Communication and Marketing agency needs a new presentation card

We are a group of communication and marketing agencies specialized in companies that are in the logistics and industrial sector. The head agency is TELVANO Grupo and the group consists of 4 agencies: TELVANO Media, TELVANO Digital, TELVANO Research and DifundeEnPantalla. We hace 4 offices in Spain (Madrid, Barcelona, Valencia and Murcia). We are looking for a clean and attractive design that transmits our experience, brand presence in the market and knowledge to those who receive the card.It has to maintain the colors of the logo that is attached.
Target Market(s)
logistics and industrial sector
Marketing department
Contact Information for Business Card
Clean and attractive design

```html
<!DOCTYPE html>
<html lang="es">
<head>
<meta charset="utf-8">
<title>DifundeEnPantalla – Tarjeta de presentación</title>
<link rel="stylesheet" href="https://fonts.googleapis.com/css2?family=Questrial&display=swap">
<style>
  :root {
    --backdrop: #efebe9;
    --paper: #f8f8fa;
    --brand-red: #c0202c;
    --charcoal: #3b3b3e;
    --ink: #1d1d1f;
    --white: #ffffff;
    --map-tint: rgba(255, 255, 255, 0.13);
  }
  * { box-sizing: border-box; margin: 0; padding: 0; }
  html, body {
    width: 1200px;
    height: 557px;
    overflow: hidden;
    background: var(--backdrop);
    font-family: "Questrial", "Century Gothic", sans-serif;
  }
  .card {
    position: absolute;
    top: 143px;
    width: 512px;
    height: 293px;
    overflow: hidden;
  }
  .card--front { left: 73px; background: var(--paper); }
  .card--back  { left: 626px; background: var(--brand-red); }
  .card__stripes {
    position: absolute;
    inset: 0;
    width: 512px;
    height: 293px;
  }

  /* Front */
  .brand-name {
    position: absolute;
    left: 26px;
    top: 110px;
    font-size: 31px;
    line-height: 33px;
    letter-spacing: 0.5px;
    color: var(--brand-red);
  }
  .holder {
    position: absolute;
    left: 266px;
    top: 66px;
    width: 155px;
    border-bottom: 1px solid var(--brand-red);
    padding-bottom: 6px;
  }
  .holder__name { font-size: 19.5px; line-height: 22px; color: var(--brand-red); }
  .holder__role { font-size: 15px; line-height: 18px; color: var(--ink); }
  .contact {
    position: absolute;
    left: 249px;
    top: 123px;
    list-style: none;
    font-size: 14px;
    color: var(--ink);
  }
  .contact__item {
    display: flex;
    align-items: flex-start;
    gap: 9px;
    line-height: 17px;
    margin-bottom: 9.5px;
  }
  .contact__icon { width: 11px; height: 11px; margin-top: 3px; flex: none; }

  /* Back */
  .world-map {
    position: absolute;
    left: 60px;
    top: 45px;
    width: 392px;
    height: 215px;
    border-radius: 40px 60px 50px 70px;
    background: var(--map-tint);
  }
  .brand-mark {
    position: absolute;
    left: 0;
    right: 0;
    top: 110px;
    text-align: center;
    font-size: 36px;
    line-height: 38px;
    color: var(--white);
  }
  .agencies {
    position: absolute;
    left: 50px;
    top: 219px;
    display: flex;
    list-style: none;
  }
  .agency {
    width: 103px;
    text-align: center;
    color: var(--white);
    font-size: 14px;
    line-height: 15px;
    border-left: 1px solid rgba(255, 255, 255, 0.7);
    padding: 2px 0;
  }
  .agency:first-child { border-left: none; }
  .agency__unit { font-size: 10px; }
</style>
</head>
<body>

<section class="card card--front" aria-label="Tarjeta, cara frontal">
  <svg class="card__stripes" viewBox="0 0 598 342" aria-hidden="true">
    <polygon points="420,0 598,0 598,205" fill="var(--charcoal)"/>
    <line x1="398" y1="-10" x2="515" y2="128" stroke="var(--brand-red)" stroke-width="12"/>
    <line x1="445" y1="-10" x2="585" y2="150" stroke="var(--white)" stroke-width="10"/>
    <polygon points="0,205 0,342 145,342" fill="var(--charcoal)"/>
    <line x1="40" y1="233" x2="155" y2="352" stroke="var(--brand-red)" stroke-width="11"/>
    <line x1="30" y1="266" x2="112" y2="352" stroke="var(--white)" stroke-width="10"/>
  </svg>

  <div class="brand-name">Difunde<br>EnPantalla</div>

  <div class="holder">
    <p class="holder__name">Lucas Moreno</p>
    <p class="holder__role">Director</p>
  </div>

  <ul class="contact">
    <li class="contact__item">
      <svg class="contact__icon" viewBox="0 0 12 12" aria-hidden="true"><rect x="3" y="0.5" width="6" height="11" rx="1.2" fill="var(--brand-red)"/><rect x="4.3" y="2" width="3.4" height="6.5" fill="var(--paper)"/></svg>
      <span>0912 48 30571</span>
    </li>
    <li class="contact__item">
      <svg class="contact__icon" viewBox="0 0 12 12" aria-hidden="true"><rect x="0.5" y="2.5" width="11" height="7.5" fill="var(--brand-red)"/><polyline points="0.8,3 6,7 11.2,3" fill="none" stroke="var(--paper)" stroke-width="1"/></svg>
      <span>hola@difundepant.com</span>
    </li>
    <li class="contact__item">
      <svg class="contact__icon" viewBox="0 0 12 12" aria-hidden="true"><circle cx="6" cy="6" r="5.5" fill="var(--brand-red)"/><line x1="0.5" y1="6" x2="11.5" y2="6" stroke="var(--paper)" stroke-width="0.9"/><ellipse cx="6" cy="6" rx="2.4" ry="5.5" fill="none" stroke="var(--paper)" stroke-width="0.9"/></svg>
      <span>www.difundepant.com</span>
    </li>
    <li class="contact__item">
      <svg class="contact__icon" viewBox="0 0 12 12" aria-hidden="true"><path d="M6 0.5a3.5 3.5 0 0 1 3.5 3.5c0 2.6-3.5 6-3.5 6s-3.5-3.4-3.5-6A3.5 3.5 0 0 1 6 0.5z" fill="var(--brand-red)"/><circle cx="6" cy="4" r="1.2" fill="var(--paper)"/><line x1="1" y1="11.3" x2="11" y2="11.3" stroke="var(--brand-red)" stroke-width="1"/></svg>
      <span>2204/56 calle norte,<br>valencia 46001</span>
    </li>
  </ul>
</section>

<section class="card card--back" aria-label="Tarjeta, cara posterior">
  <div class="world-map" role="img" aria-label="Mapamundi en tono rojo claro como fondo"></div>

  <svg class="card__stripes" viewBox="0 0 598 342" aria-hidden="true">
    <polygon points="440,0 598,0 598,190" fill="var(--charcoal)"/>
    <line x1="425" y1="-10" x2="530" y2="123" stroke="var(--white)" stroke-width="9"/>
    <line x1="470" y1="-10" x2="578" y2="128" stroke="var(--white)" stroke-width="9"/>
    <polygon points="0,262 0,342 92,342" fill="var(--charcoal)"/>
    <line x1="20" y1="276" x2="95" y2="352" stroke="var(--white)" stroke-width="9"/>
    <line x1="0" y1="300" x2="52" y2="352" stroke="var(--white)" stroke-width="9"/>
  </svg>

  <div class="brand-mark">Difunde<br>EnPantalla</div>

  <ul class="agencies">
    <li class="agency">TELVANO<br><span class="agency__unit">Digital</span></li>
    <li class="agency">TELVANO<br><span class="agency__unit">Media</span></li>
    <li class="agency">TELVANO<br><span class="agency__unit">Grupo</span></li>
    <li class="agency">TELVANO<br><span class="agency__unit">Research</span></li>
  </ul>
</section>

</body>
</html>
```